National Networking/Telecommunications Company needs a new packaging (bag) design

We are currently going through a re-branding stage and need to create new packaging for all of our material.

We need a complete redesign of our current packaging (which is in various sizes). I have attached the current die-lines/knife for one of our bags.

- VORTELL logos to be changed to our BRANQOR logo (attached)
- BRANQOR logo to be modified, so it simply says the word BRANQOR with the tick image on the end. Please remove all other writing (PROVEN SYSTEMS & WIDE RANGE, LASTING QUALITY) removed from the logo. Once this has been removed, please resize the word BRANQOR, so it fits nicely beside the tick logo.
- Please remove all references to VORTELL websites, and replace with www.branqor.com.au
- Remove "Network, Computer and Audio Video Connectivity Solutions"
- Keeping the logos that say "Lifetime Warranty" and "100% Tested and Certified", open to different ideas on how to portray them on the bag.
- Our main company colours are red, blue & silver. We're open to all designs. Packaging needs to STAND OUT, without looking cheap. Needs to still look professional and classy.
- The inside backing of the bag is to be white in colour.

I have attached our new cable box design, if that helps with keeping the colours the same.

Target Market(s)

Electrical wholesalers (who stock this product), IT/System Integrators, Installers

Industry/Entity Type

Telecommunications

Font styles to use
Sans Serif

Requirements
Must have
• Our company colours (blue, red, white/silver)
Nice to have
• Overall design needs to be simplistic, yet elegant and professional.
Should not have
• Should not have the word VORTELL anywhere

```html
<!DOCTYPE html>
<html lang="en">
<head>
<meta charset="utf-8">
<title>BRANQOR – Hang Bag Front Panel</title>
<link rel="stylesheet" href="https://fonts.googleapis.com/css2?family=Archivo:wght@400;600;700&display=swap">
<style>
  :root {
    --page-bg: #ffffff;
    --brand-navy: #10123a;
    --brand-red: #ee1c2e;
    --brand-silver: #c3c7cc;
    --panel-white: #ffffff;
    --dieline: #3a3a3a;
    --dimension: #2b8fd8;
    --dimension-label: #555a60;
    --badge-ring: #9aa0a8;
  }
  html, body {
    margin: 0;
    padding: 0;
    width: 1200px;
    height: 2429px;
    overflow: hidden;
    background: var(--page-bg);
  }
  .artboard {
    display: block;
    width: 1200px;
    height: 2429px;
  }
  .dieline-edge { fill: none; stroke: var(--dieline); stroke-width: 0.25; }
  .header-panel { fill: var(--panel-white); }
  .fold-line { stroke: var(--dieline); stroke-width: 0.25; }
  .hang-slot { fill: none; stroke: var(--dieline); stroke-width: 0.3; }
  .brand-band { fill: var(--brand-navy); }
  .arc-red { fill: var(--brand-red); }
  .arc-white, .panel-base { fill: var(--panel-white); }
  .brand-name {
    font-family: "Archivo", sans-serif;
    font-weight: 700;
    font-size: 13px;
    fill: var(--brand-silver);
  }
  .brand-dot { fill: var(--brand-red); }
  .web-address {
    font-family: "Archivo", sans-serif;
    font-weight: 600;
    font-size: 4.4px;
    letter-spacing: 0.55px;
    fill: var(--brand-red);
  }
  .badge { fill: var(--panel-white); stroke: var(--badge-ring); stroke-width: 0.6; }
  .dim-line { stroke: var(--dimension); stroke-width: 0.25; fill: none; }
  .dim-label {
    font-family: "Archivo", sans-serif;
    font-weight: 400;
    font-size: 3.2px;
    fill: var(--dimension-label);
  }
</style>
</head>
<body>
<svg class="artboard" viewBox="0 0 351.6 711.6" xmlns="http://www.w3.org/2000/svg" aria-label="BRANQOR hang bag front panel with dimensions">
  <defs>
    <clipPath id="bag-shape">
      <rect x="0" y="0" width="150" height="240"/>
    </clipPath>
  </defs>

  <g class="bag" transform="translate(100.8 235.8)">
    <g clip-path="url(#bag-shape)">
      <rect class="panel-base" x="0" y="0" width="150" height="240"/>
      <rect class="header-panel" x="0" y="0" width="150" height="45"/>
      <rect class="brand-band" x="0" y="45" width="150" height="125"/>
      <circle class="arc-red" cx="75" cy="215.5" r="101.5"/>
      <circle class="arc-white" cx="75" cy="215.5" r="94.5"/>
    </g>

    <line class="fold-line" x1="0" y1="15.5" x2="150" y2="15.5"/>
    <path class="hang-slot" d="M63 35 H89 Q90.5 35 90.5 33.3 Q90.5 31.5 88.5 31.5 H80.5 Q80 27.8 76 27.8 Q72 27.8 71.5 31.5 H63.5 Q61.5 31.5 61.5 33.3 Q61.5 35 63 35 Z"/>

    <g class="logo">
      <text class="brand-name" x="19" y="71" textLength="78" lengthAdjust="spacingAndGlyphs">BRANQOR</text>
      <circle class="brand-dot" cx="103" cy="66.2" r="4.6"/>
    </g>

    <text class="web-address" x="42" y="101.5" textLength="67" lengthAdjust="spacing">www.branqor.com.au</text>

    <circle class="badge warranty-badge" cx="19" cy="106.5" r="9"/>
    <circle class="badge tested-badge" cx="136" cy="107" r="8"/>

    <rect class="dieline-edge" x="0" y="0" width="150" height="240"/>

    <g class="dimensions">
      <line class="dim-line" x1="0" y1="-8" x2="150" y2="-8"/>
      <line class="dim-line" x1="0" y1="-10" x2="0" y2="-1"/>
      <line class="dim-line" x1="150" y1="-10" x2="150" y2="-1"/>
      <rect x="67" y="-10" width="16" height="4" fill="var(--page-bg)"/>
      <text class="dim-label" x="75" y="-7" text-anchor="middle">150mm</text>

      <line class="dim-line" x1="-8" y1="0" x2="-8" y2="240"/>
      <line class="dim-line" x1="-10" y1="0" x2="-1" y2="0"/>
      <line class="dim-line" x1="-10" y1="240" x2="-1" y2="240"/>
      <rect x="-10" y="112" width="4" height="16" fill="var(--page-bg)"/>
      <text class="dim-label" x="-7" y="120" text-anchor="middle" transform="rotate(-90 -7 120)">240mm</text>

      <line class="dim-line" x1="1" y1="0" x2="22" y2="0" transform="translate(150 0)"/>
      <line class="dim-line" x1="3" y1="0" x2="3" y2="15.5" transform="translate(150 0)"/>
      <text class="dim-label" x="154" y="8.5">15mm</text>

      <line class="dim-line" x1="151" y1="15.5" x2="164" y2="15.5"/>
      <line class="dim-line" x1="161" y1="15.5" x2="161" y2="35"/>
      <line class="dim-line" x1="151" y1="35" x2="164" y2="35"/>
      <text class="dim-label" x="155" y="25">20mm</text>

      <line class="dim-line" x1="170" y1="0" x2="170" y2="45"/>
      <line class="dim-line" x1="151" y1="45" x2="173" y2="45"/>
      <text class="dim-label" x="166" y="30">45mm</text>

      <line class="dim-line" x1="155" y1="45" x2="155" y2="127"/>
      <line class="dim-line" x1="151" y1="127" x2="158" y2="127"/>
      <text class="dim-label" x="156.5" y="87">82mm</text>
    </g>
  </g>
</svg>
</body>
</html>
```